Hollow Mesa Farm Vault Reserve Wine Label (Front and Back)

I need to create an elite tier wine label.  I would like it to be in a light, natural color with silver or gold.  I would like it to look rich and expensive, mostly monochromatic, elegantly simple.  It will need to stand up next to wine labels that are black and charcoal colored and look like the more expensive wine of the 3.  I have attached a similar label that it will be grouped with and some instructions.
We are a winery in southeast Washington state with a reputation for fine wines and top notch terroir.  We want to present family, tradition and high value wine in the bottle.

```html
<!DOCTYPE html>
<html lang="en">
<head>
<meta charset="utf-8">
<title>Hollow Mesa Farm – Vault Reserve Label</title>
<link href="https://fonts.googleapis.com/css2?family=Cinzel:wght@400;500&family=Great+Vibes&family=Libre+Baskerville&display=swap" rel="stylesheet">
<style>
  :root {
    --backdrop: #e8e8e8;
    --paper: #f7f7f6;
    --paper-edge: #eeeeec;
    --ink: #3f3f3f;
    --ink-soft: #555555;
    --gold: #c08a2e;
    --gold-light: #e2bd5e;
    --gold-deep: #b07c22;
    --silver: #d4d6d9;
    --silver-light: #eef0f2;
  }
  * { margin: 0; padding: 0; box-sizing: border-box; }
  html, body {
    width: 1200px; height: 2775px; overflow: hidden;
    background: var(--backdrop);
  }
  .canvas { position: relative; width: 1200px; height: 2775px; }
  .label {
    position: absolute; left: 100px; top: 577px;
    width: 1000px; height: 1620px;
    background: linear-gradient(180deg, var(--paper) 0%, var(--paper-edge) 100%);
    box-shadow: 0 2px 10px rgba(0,0,0,0.08);
    text-align: center; color: var(--ink);
  }
  .label > * { position: absolute; left: 0; right: 0; }
  .winery-name {
    top: 140px;
    font-family: "Cinzel", serif; font-weight: 400;
    font-size: 100px; line-height: 132px; letter-spacing: 1px;
    color: var(--ink);
    text-shadow: 2px 2px 0 rgba(0,0,0,0.12);
  }
  .region {
    top: 500px;
    font-family: "Libre Baskerville", serif;
    font-size: 40px; letter-spacing: 9px; color: var(--ink-soft);
  }
  .crest-row { top: 640px; height: 250px; }
  .wing {
    position: absolute; top: 85px; width: 270px; height: 80px;
  }
  .wing-left { left: 40px; background: linear-gradient(90deg, rgba(212,214,217,0) 0%, var(--silver) 60%, var(--silver-light) 100%); }
  .wing-right { right: 40px; background: linear-gradient(270deg, rgba(212,214,217,0) 0%, var(--silver) 60%, var(--silver-light) 100%); }
  .house-mark {
    position: absolute; left: 310px; right: 310px; top: 0; height: 250px;
    display: flex; align-items: center; justify-content: center; gap: 14px;
  }
  .house-mark .mark-square {
    width: 28px; height: 28px; border: 3px solid var(--gold); flex: none;
  }
  .house-mark .mark-name {
    font-family: "Cinzel", serif; font-weight: 400;
    font-size: 24px; letter-spacing: 2px; color: var(--gold);
    white-space: nowrap;
  }
  .vineyard {
    top: 990px;
    font-family: "Libre Baskerville", serif;
    font-size: 40px; letter-spacing: 2px; color: var(--ink);
  }
  .cuvee {
    top: 1085px;
    font-family: "Cinzel", serif; font-weight: 500;
    font-size: 86px; letter-spacing: 2px; color: var(--ink);
    text-shadow: 2px 2px 0 rgba(0,0,0,0.12);
  }
  .varietal {
    top: 1215px;
    font-family: "Great Vibes", cursive;
    font-size: 70px; color: var(--gold);
  }
  .vintage {
    top: 1345px;
    font-family: "Libre Baskerville", serif;
    font-size: 36px; color: var(--ink);
  }
  .heritage-band {
    top: 1520px; left: 30px; right: 30px; height: 72px;
    background: linear-gradient(180deg, var(--gold-light) 0%, var(--gold) 55%, var(--gold-deep) 100%);
    display: flex; align-items: center; justify-content: center;
    font-family: "Libre Baskerville", serif;
    font-size: 28px; letter-spacing: 0.5px; color: #4a3a18;
  }
</style>
</head>
<body>
  <main class="canvas">
    <section class="label">
      <h1 class="winery-name">HOLLOW MESA<br>FARM</h1>
      <p class="region">HORSE HEAVEN HILLS</p>
      <div class="crest-row">
        <div class="wing wing-left" role="img" aria-label="Silver ornamental flourish"></div>
        <div class="house-mark">
          <span class="mark-square"></span>
          <span class="mark-name">HOLLOW MESA FARM</span>
        </div>
        <div class="wing wing-right" role="img" aria-label="Silver ornamental flourish"></div>
      </div>
      <p class="vineyard">ESTATE VINEYARD</p>
      <h2 class="cuvee">VAULT RESERVE</h2>
      <p class="varietal">Cabernet Sauvignon</p>
      <p class="vintage">2022</p>
      <p class="heritage-band">FAMILY STEWARDS OF THE LAND FOR 5 GENERATIONS</p>
    </section>
  </main>
</body>
</html>
```